Business Card Design Project

We need a new fresh business card for our business. There are multiple services we offer and we need a fresh corporate card that represents us better. We start from cleaning carpet and tiles, to upholstery and curtains, to completely clean all contents and building materials after a fire, or completely dry out a home or business after a major or minor flood event. We are open to all concepts as we want to create a new look, maybe even logo, signage, vehicle signage, uniforms.
We are open to new colours etc.

Go to www.brolvaquincare.com.au for current logo and all other past ideas

Target Market(s)

Everyone is our possible client but we are targeting more coorporate

Industry/Entity Type

Building

```html
<!DOCTYPE html>
<html lang="en">
<head>
<meta charset="utf-8">
<title>Brolvaquin Care – Business Card</title>
<link rel="stylesheet" href="https://fonts.googleapis.com/css2?family=Exo+2:wght@400;500;600&display=swap">
<style>
  :root {
    --page: #e9eaec;
    --card: #ffffff;
    --card-shade: #f1f2f4;
    --brand-blue: #2b5aa6;
    --brand-pink: #e4197a;
    --ink: #4a4c52;
    --on-blue: #ffffff;
  }
  * { box-sizing: border-box; margin: 0; padding: 0; }
  html, body { width: 1200px; height: 900px; overflow: hidden; }
  body {
    background: var(--page);
    font-family: "Exo 2", sans-serif;
    position: relative;
  }
  .card {
    position: absolute;
    left: 260px;
    width: 680px;
    height: 388px;
    border-radius: 30px;
    overflow: hidden;
    background: linear-gradient(160deg, var(--card) 55%, var(--card-shade));
    box-shadow: 0 6px 22px rgba(0,0,0,.12);
  }
  .card--front { top: 44px; }
  .card--back { top: 468px; }
  .card__waves { position: absolute; inset: 0; width: 100%; height: 100%; }

  .brand { position: absolute; display: flex; align-items: center; gap: 12px; }
  .brand__name {
    font-weight: 600;
    color: var(--brand-blue);
    white-space: nowrap;
  }
  .brand__dot {
    border-radius: 50%;
    background: var(--brand-blue);
  }
  .card--front .brand { left: 40px; top: 40px; }
  .card--front .brand__name { font-size: 30px; }
  .card--front .brand__dot { width: 38px; height: 38px; }

  .card--back .brand { left: 50%; top: 50%; transform: translate(-50%, -50%); gap: 20px; }
  .card--back .brand__name { font-size: 50px; }
  .card--back .brand__dot { width: 64px; height: 64px; }

  .person { position: absolute; right: 44px; top: 62px; text-align: right; }
  .person__name { font-size: 22px; font-weight: 500; letter-spacing: 1px; color: var(--ink); }
  .person__role { font-size: 16px; color: var(--brand-blue); margin-top: 4px; }

  .contact {
    position: absolute;
    right: 40px;
    top: 236px;
    list-style: none;
    text-align: right;
    color: var(--on-blue);
    font-size: 13px;
    line-height: 22px;
  }
  .contact__item { display: flex; justify-content: flex-end; align-items: center; gap: 8px; }
  .contact__icon { width: 12px; height: 12px; fill: var(--on-blue); flex: none; }
  .contact__spacer { width: 12px; flex: none; }
</style>
</head>
<body>

<section class="card card--front" aria-label="Business card front">
  <svg class="card__waves" viewBox="0 0 680 388" preserveAspectRatio="none" aria-hidden="true">
    <path d="M0,168 C170,170 330,250 680,212 L680,238 C330,276 170,202 0,204 Z" fill="var(--brand-pink)"/>
    <path d="M0,200 C170,198 330,272 680,234 L680,388 L0,388 Z" fill="var(--brand-blue)"/>
  </svg>

  <div class="brand">
    <span class="brand__name">Brolvaquin Care</span>
    <span class="brand__dot"></span>
  </div>

  <div class="person">
    <p class="person__name">MARTIN KELLER</p>
    <p class="person__role">Managing Director</p>
  </div>

  <ul class="contact">
    <li class="contact__item">14 Harbour Vale Drive
      <svg class="contact__icon" viewBox="0 0 12 12"><path d="M6 0a4 4 0 0 0-4 4c0 3 4 8 4 8s4-5 4-8a4 4 0 0 0-4-4zm0 5.5A1.5 1.5 0 1 1 6 2.5a1.5 1.5 0 0 1 0 3z"/></svg>
    </li>
    <li class="contact__item">Westbrook NSW 2150 <span class="contact__spacer"></span></li>
    <li class="contact__item">02 9481 3067
      <svg class="contact__icon" viewBox="0 0 12 12"><path d="M2.5 0.5l2 2.5-1.2 1.4a7 7 0 0 0 4.3 4.3L9 7.5l2.5 2-1.3 2A9.5 9.5 0 0 1 0.5 1.8z"/></svg>
    </li>
    <li class="contact__item">0412 583 906
      <svg class="contact__icon" viewBox="0 0 12 12"><path d="M3 0h6a1 1 0 0 1 1 1v10a1 1 0 0 1-1 1H3a1 1 0 0 1-1-1V1a1 1 0 0 1 1-1zm0 1.5v8h6v-8z"/></svg>
    </li>
    <li class="contact__item">info@brolvaquincare.com.au
      <svg class="contact__icon" viewBox="0 0 12 12"><path d="M0 2h12v8H0zm1 1v.4l5 3.3 5-3.3V3z"/></svg>
    </li>
    <li class="contact__item">www.brolvaquincare.com.au
      <svg class="contact__icon" viewBox="0 0 12 12"><path d="M6 0a6 6 0 1 0 0 12A6 6 0 0 0 6 0zm0 1.2c.8.9 1.3 2.4 1.4 4.2H4.6C4.7 3.6 5.2 2.1 6 1.2zM1.3 6.6h2.3c.1 1.6.5 3 1.1 4A4.8 4.8 0 0 1 1.3 6.6zm0-1.2a4.8 4.8 0 0 1 3.4-4c-.6 1-1 2.4-1.1 4zm4.7 5.4c-.8-.9-1.3-2.4-1.4-4.2h2.8c-.1 1.8-.6 3.3-1.4 4.2zm1.3-.2c.6-1 1-2.4 1.1-4h2.3a4.8 4.8 0 0 1-3.4 4zm1.1-5.2c-.1-1.6-.5-3-1.1-4a4.8 4.8 0 0 1 3.4 4z"/></svg>
    </li>
  </ul>
</section>

<section class="card card--back" aria-label="Business card back">
  <div class="brand">
    <span class="brand__name">Brolvaquin Care</span>
    <span class="brand__dot"></span>
  </div>
</section>

</body>
</html>
```